Marwick Family Chiropractic Stationary

The letterhead and business card must have our logo.
We would like to see the logo used in different ways ( It can be expanded upon in the stationary.)
Please use the the same or similar colors.
Must be eye catching and memorable.
Must be easy to read

Reason: The doctor has been too busy to make any final decisions. He would like to give himself a little more time.

Target Market(s)

Chiropractic Healthcare

Industry/Entity Type

Business

Requirements
Must have
• Dr. Leonard Marwick D.C.
Chiropractor

555-555-0183

417 Birchfield Road, 2nd Floor
Larchmere, ZZ 06091

drmarwick@marwickspine.example
www.marwickspine.example
www.facebook.com/MarwickFamilySpine
Should not have
• should not be difficult to read

```html
<!DOCTYPE html>
<html lang="en">
<head>
<meta charset="utf-8">
<title>Marwick Family Chiropractic Letterhead</title>
<link rel="stylesheet" href="https://fonts.googleapis.com/css2?family=Varela+Round&display=swap">
<style>
  :root {
    --green: #2a9446;
    --yellow: #f2e600;
    --ink: #231f20;
    --paper: #ffffff;
  }
  html, body {
    margin: 0;
    padding: 0;
    overflow: hidden;
    background: var(--paper);
  }
  .letterhead {
    position: relative;
    width: 848px;
    height: 1200px;
    background: var(--paper);
    font-family: "Varela Round", sans-serif;
    color: var(--ink);
    overflow: hidden;
  }
  .brand {
    position: absolute;
    left: 36px;
    top: 38px;
    width: 162px;
    text-align: center;
  }
  .brand-dot {
    display: block;
    width: 100px;
    height: 100px;
    margin: 0 auto 14px;
    border-radius: 50%;
    background: var(--green);
  }
  .brand-name {
    margin: 0;
    color: var(--green);
    font-size: 14px;
    font-weight: 400;
    line-height: 1.3;
    letter-spacing: 0.4px;
    -webkit-text-stroke: 0.4px var(--green);
  }
  .tagline {
    position: absolute;
    right: 38px;
    top: 36px;
    margin: 0;
    font-size: 22px;
    font-weight: 400;
    letter-spacing: 0.3px;
  }
  .tagline .accent { color: var(--green); -webkit-text-stroke: 0.5px var(--green); }
  .tagline .strong { color: var(--ink); -webkit-text-stroke: 0.7px var(--ink); }
  .edge-bar {
    position: absolute;
    right: 0;
    top: 174px;
    width: 9px;
    height: 846px;
  }
  .contact {
    position: absolute;
    left: 39px;
    top: 1066px;
    font-size: 9.6px;
    line-height: 12px;
    -webkit-text-stroke: 0.25px var(--ink);
  }
  .contact p { margin: 0; white-space: nowrap; }
  .contact .doctor {
    font-size: 13.5px;
    line-height: 15px;
    letter-spacing: 0.2px;
    -webkit-text-stroke: 0.4px var(--ink);
  }
  .contact .role {
    letter-spacing: 11.6px;
    font-size: 9px;
    line-height: 10px;
  }
  .contact .hl { color: var(--green); -webkit-text-stroke: 0.25px var(--green); }
</style>
</head>
<body>
<main class="letterhead">
  <header>
    <div class="brand">
      <span class="brand-dot" aria-hidden="true"></span>
      <p class="brand-name">Marwick<br>Family Chiropractic</p>
    </div>
    <h1 class="tagline"><span class="accent">Chiropractic</span> <span class="strong">Healthcare</span></h1>
  </header>

  <svg class="edge-bar" viewBox="0 0 9 846" aria-hidden="true">
    <polygon points="9,0 9,218 0,218 0,12" fill="var(--green)"/>
    <rect x="0" y="218" width="9" height="451" fill="var(--yellow)"/>
    <polygon points="0,669 9,669 9,846 0,830" fill="var(--green)"/>
  </svg>

  <footer class="contact">
    <p class="doctor">Dr. Leonard Marwick D.C.</p>
    <p class="role">Chiropractor</p>
    <p class="hl">555-555-0183</p>
    <p><span class="hl">417</span> Birchfield Road, 2nd Floor</p>
    <p>Larchmere, ZZ <span class="hl">06091</span></p>
    <p>drmarwick@marwickspine.example</p>
    <p>www.marwickspine.example</p>
    <p>www.facebook.com/MarwickFamilySpine</p>
  </footer>
</main>
</body>
</html>
```